Business Card Design For A Renovation Contractor Company

We need a business card for a new company based in Singapore, our company name is "RB Tolvane". We are a renovation contractor that builds designs into reality. We build more of F&B restaurants, retail stores and commercial offices. We work very closely with designers. The final design should communicate to our client that we are a company that you can trust, that will plan and complete your project without giving you a headache. I like my client to remember my company as "RB". The beauty of SIMPLE is important.

Industry/Entity Type

Contractor

Requirements
Nice to have
• Black or Red base

```html
<!DOCTYPE html>
<html lang="en">
<head>
<meta charset="utf-8">
<title>RB Tolvane — Business Card</title>
<link rel="stylesheet" href="https://fonts.googleapis.com/css2?family=Montserrat:wght@300;400&family=Open+Sans:wght@400;700&display=swap">
<style>
  :root {
    --red: #e51c24;
    --black: #121012;
    --ink: #1d1d1d;
    --paper: #ffffff;
    --backdrop: #e6e6ea;
    --divider: #d6d6d6;
  }
  * { margin: 0; padding: 0; box-sizing: border-box; }
  html, body { width: 1200px; height: 987px; overflow: hidden; }
  body {
    background: var(--backdrop);
    position: relative;
    font-family: "Open Sans", Arial, sans-serif;
    color: var(--ink);
  }
  .card {
    position: absolute;
    border-radius: 28px;
    overflow: hidden;
    box-shadow: 0 10px 30px rgba(0,0,0,0.15);
  }
  .card-back {
    left: 560px; top: 70px; width: 590px; height: 340px;
    background: var(--red);
    display: flex; flex-direction: column; align-items: center; justify-content: center;
  }
  .back-brand {
    display: flex; align-items: center; gap: 18px;
    font-family: "Montserrat", Arial, sans-serif;
    font-weight: 400; font-size: 58px; color: var(--black);
    letter-spacing: 1px;
  }
  .back-brand .mark-dot {
    width: 30px; height: 30px; border-radius: 50%;
    background: var(--black);
  }
  .back-url {
    margin-top: 34px;
    color: var(--paper);
    font-size: 17px;
    letter-spacing: 6px;
  }
  .card-front {
    left: 50px; top: 430px; width: 600px; height: 345px;
    background: var(--paper);
  }
  .front-waves { position: absolute; inset: 0; }
  .brand {
    position: absolute; left: 34px; top: 40px;
  }
  .brand-name {
    display: flex; align-items: center; gap: 12px;
    font-family: "Montserrat", Arial, sans-serif;
    font-weight: 300; font-size: 40px; color: var(--ink);
    line-height: 1;
  }
  .brand-name .mark-dot {
    width: 20px; height: 20px; border-radius: 50%; background: var(--red);
  }
  .brand-rule {
    height: 1px; background: var(--ink); margin: 8px 0 4px;
  }
  .tagline {
    font-family: "Montserrat", Arial, sans-serif;
    font-weight: 300; font-size: 14.5px; color: var(--ink);
  }
  .divider {
    position: absolute; left: 330px; top: 40px; width: 1px; height: 200px;
    background: var(--divider);
  }
  .contact {
    position: absolute; left: 352px; top: 40px;
  }
  .person-name { font-weight: 700; font-size: 20px; line-height: 1.1; }
  .person-title { color: var(--red); font-size: 15px; margin-bottom: 10px; }
  .contact-list { list-style: none; }
  .contact-list li {
    display: flex; align-items: center; gap: 8px;
    font-size: 15px; line-height: 1.45;
  }
  .contact-list svg { width: 14px; height: 14px; flex: none; }
  .address { margin-top: 8px; font-size: 15px; line-height: 1.3; }
</style>
</head>
<body>

<section class="card card-back" aria-label="Card back">
  <div class="back-brand"><span class="mark-dot"></span>RB Tolvane</div>
  <div class="back-url">www.rbtolvane.com</div>
</section>

<section class="card card-front" aria-label="Card front">
  <svg class="front-waves" viewBox="0 0 600 345" preserveAspectRatio="none" aria-hidden="true">
    <path d="M0,112 C160,118 330,250 600,306 L600,326 C320,278 150,150 0,138 Z" fill="var(--red)"/>
    <path d="M0,146 C150,156 310,286 600,334 L600,345 L0,345 Z" fill="var(--black)"/>
    <path d="M190,176 C330,250 450,292 600,300" fill="none" stroke="var(--red)" stroke-width="2"/>
  </svg>

  <div class="brand">
    <div class="brand-name"><span class="mark-dot"></span>RB Tolvane</div>
    <div class="brand-rule"></div>
    <div class="tagline">turning plans into real spaces</div>
  </div>

  <div class="divider"></div>

  <div class="contact">
    <div class="person-name">Your Name</div>
    <div class="person-title">Title</div>
    <ul class="contact-list">
      <li>
        <svg viewBox="0 0 16 16"><circle cx="8" cy="8" r="8" fill="var(--red)"/><path d="M5 4.5l1.6-.5 1 2-1 .8a5 5 0 0 0 2.6 2.6l.8-1 2 1-.5 1.6c-3.2.2-6.7-3.3-6.5-6.5z" fill="#fff"/></svg>
        123-456-0789
      </li>
      <li>
        <svg viewBox="0 0 16 16"><rect x="4" y="1" width="8" height="14" rx="1.5" fill="var(--red)"/><rect x="5.5" y="3" width="5" height="8" fill="#fff"/></svg>
        123-456-0789
      </li>
      <li>
        <svg viewBox="0 0 16 16"><rect x="1" y="3" width="14" height="10" rx="1" fill="var(--red)"/><path d="M1.5 3.5L8 9l6.5-5.5" fill="none" stroke="#fff" stroke-width="1.3"/></svg>
        info@rbtolvane.com
      </li>
      <li>
        <svg viewBox="0 0 16 16"><circle cx="8" cy="8" r="7" fill="var(--red)"/><g fill="none" stroke="#fff" stroke-width="1"><ellipse cx="8" cy="8" rx="3" ry="7"/><path d="M1 8h14M2.5 4.5h11M2.5 11.5h11"/></g></svg>
        www.rbtolvane.com
      </li>
    </ul>
    <div class="address">Street Name, City Name<br>State Zip Code</div>
  </div>
</section>

</body>
</html>
```